Letterhead for a Natural Hair Run

We need a letterhead design with the logo uploaded entitled 'Bluevista Dash'. This run is a natural 5K run seeking to promote the acceptance of natural beauty in every aspect of society encompassing one's ethnic roots and its connection to a healthy lifetstyle. We would like to see designs coordinating with our logo. The design should be fun and exciting!

Industry/Entity Type

Hair

Font styles to use
Serif
Sans Serif

Requirements
Must have
• Please included this information on the letter head:
• P.O. Box K7142
• Nassau, Bahamas
• Phone: (242) 618-9027
• Email: tidewalker519@brinkmail.example

```html
<!DOCTYPE html>
<html lang="en">
<head>
<meta charset="utf-8">
<title>Bluevista Dash Letterhead</title>
<link href="https://fonts.googleapis.com/css2?family=Arimo:wght@400&display=swap" rel="stylesheet">
<style>
  :root {
    --backdrop: #e9e6e2;
    --paper: #ffffff;
    --band-blue: #33bcd6;
    --band-blue-deep: #27b3cf;
    --stripe-yellow: #f3e35a;
    --contact-text: #f6ea6a;
    --icon-white: #ffffff;
    --brand-ink: #1f1f1f;
  }
  * { box-sizing: border-box; margin: 0; padding: 0; }
  html, body {
    width: 992px; height: 1200px; overflow: hidden;
    background: var(--backdrop);
    font-family: "Arimo", Arial, sans-serif;
  }
  .letterhead {
    position: absolute; left: 46px; top: 18px;
    width: 900px; height: 1164px;
    background: var(--paper);
    box-shadow: 0 6px 18px rgba(0,0,0,0.18);
    overflow: hidden;
  }
  .brand {
    position: absolute; left: 70px; top: 70px;
    display: flex; align-items: center; gap: 14px;
  }
  .brand-dot {
    width: 22px; height: 22px; border-radius: 50%;
    background: var(--band-blue);
  }
  .brand-name {
    font-size: 30px; font-weight: 400; color: var(--brand-ink);
    white-space: nowrap;
  }
  .footer-stripe {
    position: absolute; left: 0; right: 0; bottom: 112px;
    height: 14px; background: var(--stripe-yellow);
  }
  .footer-band {
    position: absolute; left: 0; right: 0; bottom: 0;
    height: 112px;
    background: linear-gradient(180deg, var(--band-blue), var(--band-blue-deep));
    display: flex; align-items: center; justify-content: space-between;
    padding: 0 60px;
  }
  .contact-group { display: flex; flex-direction: column; gap: 16px; }
  .contact-item {
    display: flex; align-items: center; gap: 16px;
    color: var(--contact-text); font-size: 17px;
    white-space: nowrap;
  }
  .contact-icon { width: 24px; height: 24px; flex: none; }
</style>
</head>
<body>
  <main class="letterhead">
    <header class="brand">
      <span class="brand-dot"></span>
      <span class="brand-name">Bluevista Dash</span>
    </header>

    <div class="footer-stripe"></div>
    <footer class="footer-band">
      <div class="contact-item">
        <svg class="contact-icon" viewBox="0 0 26 26" aria-hidden="true">
          <path d="M13 3 L24 13 H20 V23 H6 V13 H2 Z" fill="var(--icon-white)"/>
          <rect x="11" y="16" width="4" height="7" fill="var(--band-blue)"/>
        </svg>
        <span>Nassau, Bahamas</span>
      </div>

      <div class="contact-group">
        <div class="contact-item">
          <svg class="contact-icon" viewBox="0 0 26 26" aria-hidden="true">
            <path d="M3 9 L13 4 L23 9 V20 H3 Z" fill="var(--icon-white)"/>
            <rect x="7" y="10" width="12" height="3" fill="var(--band-blue)"/>
          </svg>
          <span>P.O. Box K7142</span>
        </div>
        <div class="contact-item">
          <svg class="contact-icon" viewBox="0 0 26 26" aria-hidden="true">
            <rect x="2" y="6" width="22" height="15" fill="var(--icon-white)"/>
            <path d="M2 6 L13 15 L24 6" fill="none" stroke="var(--band-blue)" stroke-width="2"/>
          </svg>
          <span>Email: tidewalker519@brinkmail.example</span>
        </div>
      </div>

      <div class="contact-item">
        <svg class="contact-icon" viewBox="0 0 26 26" aria-hidden="true">
          <path d="M7 3 L11 8 L8.5 11 C10 14.5 11.5 16 15 17.5 L18 15 L23 19 L20 23 C11 22 4 15 3 6 Z" fill="var(--icon-white)"/>
        </svg>
        <span>Phone: (242) 618-9027</span>
      </div>
    </footer>
  </main>
</body>
</html>
```